Business Card - connecting 2 souls and beggining the journey of self discovery

Logo on the front
with tag line

On the back list of services and contact details

Seminars
workshops
Coaching
podcasts

Darren Whitlow
Health & Wellbeing Life Coach
0491 372 615
darren@brightcoreliving.example
brightcoreliving.example

Industry/Entity Type

Life Coaching

Contact Information for Business Card

I like the use of colour from the logo to be used. I'm not a fan of white.

Requirements
Must have
• My tagline: The journey home starts with you
Nice to have
• Use of colour that is in the mind body soul logo

```html
<!DOCTYPE html>
<html lang="en">
<head>
<meta charset="utf-8">
<title>Brightcore Living – Business Card</title>
<link href="https://fonts.googleapis.com/css2?family=Montserrat:wght@500&family=Open+Sans:wght@400;600&family=Oswald:wght@500&display=swap" rel="stylesheet">
<style>
  :root {
    --backdrop: #1b1b1c;
    --card: #262627;
    --ink-white: #f4f4f4;
    --ink-grey: #8a8a8a;
    --leaf: #8cc63f;
    --violet: #8e55b5;
    --rose: #e07d9a;
    --green: #7dc24a;
    --sun: #f6b72c;
    --coral: #f0606e;
  }
  * { box-sizing: border-box; margin: 0; padding: 0; }
  html, body { width: 1200px; height: 1000px; overflow: hidden; }
  body {
    background: var(--backdrop);
    font-family: "Open Sans", Arial, sans-serif;
    position: relative;
  }
  .card {
    position: absolute;
    left: 240px;
    width: 720px;
    height: 410px;
    background: var(--card);
    border-radius: 3px;
    box-shadow: 0 10px 30px rgba(0,0,0,.5);
    overflow: hidden;
  }
  .card--front { top: 60px; }
  .card--back { top: 530px; }

  /* Front */
  .brand {
    position: absolute;
    top: 110px; left: 0; right: 0;
    display: flex; flex-direction: column; align-items: center; gap: 22px;
  }
  .brand__dot {
    width: 84px; height: 84px; border-radius: 50%;
    background: var(--green);
  }
  .brand__name {
    font-family: "Montserrat", Arial, sans-serif;
    font-weight: 500;
    font-size: 28px;
    letter-spacing: -0.5px;
    color: var(--ink-grey);
  }
  .tagline {
    position: absolute;
    bottom: 48px; left: 0; right: 0;
    text-align: center;
    font-size: 19px;
    letter-spacing: 1.5px;
  }
  .tagline .t1 { color: var(--sun); }
  .tagline .t2 { color: var(--green); }
  .tagline .t3 { color: var(--rose); }
  .tagline .t4 { color: var(--coral); }

  /* Back */
  .identity {
    position: absolute;
    top: 120px; right: 420px;
    text-align: right;
  }
  .identity__name {
    font-family: "Oswald", Arial, sans-serif;
    font-weight: 500;
    font-size: 38px;
    letter-spacing: 1px;
    color: var(--ink-white);
    text-transform: uppercase;
    line-height: 1.1;
  }
  .identity__role {
    font-size: 22px;
    font-weight: 600;
    color: var(--leaf);
    margin-top: 2px;
  }
  .divider {
    position: absolute;
    top: 125px; left: 318px;
    width: 2px; height: 78px;
    background: var(--ink-white);
  }
  .contacts {
    position: absolute;
    top: 124px; left: 340px;
    list-style: none;
    font-size: 18px;
    color: var(--ink-white);
    line-height: 27px;
  }
  .contacts li { display: flex; align-items: center; gap: 12px; }
  .contacts svg { width: 16px; height: 16px; flex: none; }
  .contacts .hl { color: var(--leaf); }
  .services {
    position: absolute;
    left: 0; right: 0; bottom: 0;
    height: 62px;
    background: linear-gradient(90deg, var(--violet) 0%, var(--rose) 18%, var(--green) 42%, var(--sun) 72%, var(--coral) 100%);
    display: flex; align-items: center;
    padding-left: 36px;
    font-size: 21px;
    font-weight: 600;
    letter-spacing: 1px;
    color: var(--ink-white);
    text-transform: uppercase;
    white-space: nowrap;
  }
</style>
</head>
<body>
  <section class="card card--front">
    <div class="brand">
      <span class="brand__dot"></span>
      <span class="brand__name">Brightcore Living</span>
    </div>
    <p class="tagline"><span class="t1">The Journey</span> <span class="t2">home starts</span> <span class="t3">with</span> <span class="t4">you</span></p>
  </section>

  <section class="card card--back">
    <div class="identity">
      <h1 class="identity__name">Darren Whitlow</h1>
      <p class="identity__role">Life Coach</p>
    </div>
    <span class="divider"></span>
    <ul class="contacts">
      <li>
        <svg viewBox="0 0 16 16"><rect x="4" y="1" width="8" height="14" rx="1.5" fill="none" stroke="#8cc63f" stroke-width="1.6"/><circle cx="8" cy="12.3" r="0.9" fill="#8cc63f"/></svg>
        0491 372 615
      </li>
      <li>
        <svg viewBox="0 0 16 16"><rect x="1" y="3" width="14" height="10" fill="#8cc63f"/><path d="M1 3 L8 9 L15 3" fill="none" stroke="#262627" stroke-width="1.3"/></svg>
        darren@brightcoreliving.example
      </li>
      <li>
        <svg viewBox="0 0 16 16"><circle cx="8" cy="8" r="6.8" fill="#8cc63f"/><path d="M1.5 8 H14.5 M8 1.2 V14.8 M8 1.2 C4 5 4 11 8 14.8 M8 1.2 C12 5 12 11 8 14.8" fill="none" stroke="#262627" stroke-width="1"/></svg>
        <span>www.<span class="hl">brightcoreliving</span>.example</span>
      </li>
    </ul>
    <div class="services">Seminars | Workshops | Coaching | Podcasts</div>
  </section>
</body>
</html>
```